Fresh Dwelling Tract Guide needs a new Landing Page

I like to get a landing page or website with 2-3 pages to help target home buyers who are looking to buy homes from builders such as TW Residences, Morvik, P.L. Fennick, etc. The landing page/website to be non-cluttered and be able to explain to home buyers that there are many benefits to include me as their buyer's agent when they buy a brand new home from any builders.
I may want to incorporate a short explanation video (animated) on the landing page and then for the viewer to click on a button that will take them to another page where they can search for new homes from different builders.
Target Market(s)
Home buyers looking to buy brand new home from builders such as TW Residences, Morvik, P.L. Fennick, etc.
Industry/Entity Type
Real Estate
Number of Pages Required
2 page
Font styles to use
Requirements
Must have
- The landing page may have the explanation video at the bottom of the landing page (scrolled down) or there may be a CALL TO ACTION button that takes the viewer to the 2nd page to watch the explanation video. Once they watched the explanation video and are still interested, they can click on another CALL TO ACTION button that will take them to another website that they will be able to search for all the available new homes and register their contact information.
Should not have
- No clutters and no dark colors.

```html
<!DOCTYPE html>
<html lang="en">
<head>
<meta charset="UTF-8">
<title>Fresh Dwelling Tract</title>
<link href="https://fonts.googleapis.com/css2?family=Oswald:wght@400&family=Poppins:wght@300;400;600&display=swap" rel="stylesheet">
<style>
  :root {
    --sky-top: #6f93c8;
    --sky-mid: #86a3cc;
    --city-mid: #9fb0c9;
    --city-warm: #c9ab80;
    --city-glow: rgba(255, 214, 140, 0.45);
    --white: #ffffff;
    --accent-red: #ff0a0a;
    --footer-band: rgba(255, 255, 255, 0.16);
    --halo: rgba(255, 255, 255, 0.28);
    --shade: rgba(40, 70, 120, 0.18);
    --ink: #1c2230;
  }
  * { margin: 0; padding: 0; box-sizing: border-box; }
  html, body { width: 1200px; height: 753px; overflow: hidden; }
  body { font-family: "Poppins", sans-serif; color: var(--white); background: var(--sky-mid); }

  .hero { position: relative; width: 1200px; height: 753px; overflow: hidden; }

  .hero-photo {
    position: absolute; inset: 0;
    background:
      radial-gradient(ellipse 60% 35% at 50% 62%, var(--city-glow), transparent 70%),
      radial-gradient(ellipse 40% 30% at 85% 45%, var(--city-glow), transparent 70%),
      radial-gradient(ellipse 40% 30% at 12% 55%, var(--city-glow), transparent 70%),
      linear-gradient(180deg, var(--sky-top) 0%, var(--sky-mid) 14%, var(--city-mid) 40%, #b5ad9f 65%, var(--city-warm) 100%);
  }
  .hero-shade { position: absolute; inset: 0; background: var(--shade); }

  .site-header { position: absolute; top: 0; left: 0; right: 0; height: 78px; }
  .brand {
    position: absolute; left: 98px; top: 22px;
    font-family: "Oswald", sans-serif; font-size: 27px; font-weight: 400;
    text-transform: uppercase; line-height: 34px;
    text-shadow: 0 1px 6px rgba(30, 50, 90, 0.35);
  }
  .contact-button {
    position: absolute; left: 903px; top: 17px; width: 147px; height: 42px;
    background: var(--accent-red); color: var(--white);
    font-size: 14px; font-weight: 400; text-transform: uppercase; letter-spacing: 0.3px;
    display: flex; align-items: center; justify-content: center; text-decoration: none;
  }
  .menu-toggle { position: absolute; left: 1083px; top: 31px; width: 18px; height: 16px; }

  .hero-content {
    position: absolute; left: 0; right: 0; top: 236px; text-align: center;
    text-shadow: 0 2px 10px rgba(30, 50, 90, 0.4);
  }
  .hero-title { font-size: 55px; font-weight: 600; line-height: 64px; }
  .hero-lead { font-size: 15.5px; font-weight: 300; line-height: 22px; margin-top: 4px; }

  .play-button { position: absolute; left: 545px; top: 348px; width: 110px; height: 110px; }

  .site-footer {
    position: absolute; left: 0; right: 0; top: 664px; bottom: 0;
    background: var(--footer-band); text-align: center;
    text-shadow: 0 1px 4px rgba(30, 50, 90, 0.4);
  }
  .social-list {
    position: absolute; top: 22px; left: 0; right: 0;
    display: flex; justify-content: center; gap: 37px; list-style: none;
  }
  .social-dot { width: 16px; height: 16px; border-radius: 50%; background: var(--white); }
  .copyright {
    position: absolute; top: 52px; left: 0; right: 0;
    font-size: 13px; font-weight: 300; line-height: 18px;
  }
</style>
</head>
<body>
<main class="hero">
  <div class="hero-photo" role="img" aria-label="Aerial evening view of a city skyline with lit towers under a soft blue sky"></div>
  <div class="hero-shade"></div>

  <header class="site-header">
    <div class="brand">Fresh Dwelling Tract</div>
    <a class="contact-button" href="#">Contact Us</a>
    <svg class="menu-toggle" viewBox="0 0 18 16" aria-label="Menu">
      <rect x="0" y="0" width="18" height="3" fill="#ffffff"/>
      <rect x="0" y="6.5" width="18" height="3" fill="#ffffff"/>
      <rect x="0" y="13" width="18" height="3" fill="#ffffff"/>
    </svg>
  </header>

  <section class="hero-content">
    <h1 class="hero-title">Fresh Dwelling Tract</h1>
    <p class="hero-lead">Lorem ipsum dolor sit amet, consectetur adipiscing elit, sed do eiusmod tempor incididunt</p>
  </section>

  <svg class="play-button" viewBox="0 0 110 110" aria-label="Play video">
    <circle cx="55" cy="55" r="55" fill="var(--halo)"/>
    <circle cx="55" cy="55" r="41" fill="#ffffff"/>
    <path d="M48 42 L68 55 L48 68 Z" fill="var(--ink)"/>
  </svg>

  <footer class="site-footer">
    <ul class="social-list">
      <li class="social-dot"></li>
      <li class="social-dot"></li>
      <li class="social-dot"></li>
      <li class="social-dot"></li>
    </ul>
    <p class="copyright">© 2018 Fresh Dwelling Tract. All Rights Reserved.</p>
  </footer>
</main>
</body>
</html>
```